New, modern business card for growing audiology practice

We need a new business card for our audiology practice. Our logo and website have recently changed (more modern) and we want our business cards to reflect this change.
We conduct hearing tests, perform earwax removals, and fit & dispense hearing aids to our patients. We are a family owned practice in which the owner is the one who works directly with the patient. I have attached logos in various formats to use, as well as two ideas I found on this website; as well as a scanned copy of our current logo. Good luck!

Industry/Entity Type

Business

Contact Information for Business Card

Company name: Tolvera Hearing Center
Provider name: Peter Wolstenby, Au.D. F/NSB
Phone number: (440) 683-5127
Address: 837 W. Lindell Ave. Brennford, OH 44190
email: tolverahearing@postvane.com
website: tolverahearing.com

Colors
000000
aaaaaa
dbdbdb
cacaca
9bcb3c
afd23c
cadf82
b1b1b1

Requirements
Must have
• My card must include information in the "details" section. In the attached images, I found a few that I liked and I would like to model after - "brisky bouncin'" and "Sound Method Center".
• Must be horizontal.
• Must include logos provided. I uploaded them in various file formats and various ways.
• Must match logo font, if possible, if not, please get as close as you can.
Nice to have
• I really like the idea of having a color on one side with just the logo and company name and the contact information and provider name on the other side. I also really like the idea of having the main color dominating on the logo/company side with accent of that same color on the contact side of the card.
Should not have
• Must not be vertical.

```html
<!DOCTYPE html>
<html lang="en">
<head>
<meta charset="utf-8">
<title>Tolvera Hearing Center – Business Card</title>
<link rel="stylesheet" href="https://fonts.googleapis.com/css2?family=Lato:wght@400&family=Roboto:wght@400;500&family=Roboto+Condensed:wght@700&display=swap">
<style>
  :root {
    --backdrop: #7a5a3e;
    --card-white: #f2f2f2;
    --card-black: #000000;
    --ink: #111111;
    --ink-soft: #555555;
    --green: #6f9f2b;
    --green-light: #9bcb3c;
    --divider: #aaaaaa;
    --white: #ffffff;
  }
  * { margin: 0; padding: 0; box-sizing: border-box; }
  html, body { width: 1200px; height: 960px; overflow: hidden; }
  body { background: var(--backdrop); position: relative; font-family: "Roboto", Arial, sans-serif; }

  .card {
    position: absolute;
    width: 600px;
    height: 342px;
    box-shadow: 0 4px 10px rgba(0,0,0,0.35);
    overflow: hidden;
  }
  .card--front { left: 314px; top: 113px; background: var(--card-white); }
  .card--back { left: 311px; top: 472px; background: var(--card-black); }

  .brand {
    position: absolute;
    display: flex;
    align-items: center;
    font-family: "Lato", "Gill Sans", sans-serif;
    font-weight: 400;
    text-transform: uppercase;
    white-space: nowrap;
  }
  .brand__dot { border-radius: 50%; background: var(--green-light); flex: none; }

  .card--front .brand { left: 48px; top: 158px; font-size: 17.5px; color: var(--ink); letter-spacing: -0.3px; }
  .card--front .brand__dot { width: 14px; height: 14px; margin-right: 10px; }

  .card--back .brand { left: 0; right: 0; top: 155px; justify-content: center; font-size: 29px; color: var(--white); letter-spacing: -0.2px; }
  .card--back .brand__dot { width: 22px; height: 22px; margin-right: 14px; }

  .divider {
    position: absolute;
    left: 323px; top: 99px;
    width: 2px; height: 148px;
    background: linear-gradient(to bottom, rgba(170,170,170,0), var(--divider) 20%, var(--divider) 80%, rgba(170,170,170,0));
  }

  .contact { position: absolute; left: 351px; top: 96px; }
  .contact__name {
    font-family: "Roboto Condensed", "Arial Narrow", sans-serif;
    font-weight: 700; font-size: 22px; color: var(--green);
    line-height: 26px; text-transform: uppercase;
  }
  .contact__title { font-weight: 500; font-size: 14px; color: var(--ink); line-height: 20px; text-transform: uppercase; }
  .contact__address { margin-top: 10px; font-size: 14px; line-height: 18px; color: var(--ink-soft); }
  .contact__lines { margin-top: 11px; list-style: none; font-size: 14px; line-height: 19px; color: var(--ink-soft); }
  .contact__lines li { display: flex; align-items: center; }
  .contact__lines svg { width: 12px; height: 12px; margin-right: 10px; fill: var(--green); flex: none; }

  .footer-band { position: absolute; left: 0; bottom: 0; width: 600px; height: 40px; }
  .footer-band__url {
    position: absolute; left: 351px; bottom: 9px;
    font-size: 14px; color: var(--white); letter-spacing: 3px;
  }
</style>
</head>
<body>

<section class="card card--front" aria-label="Business card front">
  <div class="brand">
    <span class="brand__dot"></span>
    <span class="brand__name">Tolvera Hearing Center</span>
  </div>

  <div class="divider"></div>

  <div class="contact">
    <h1 class="contact__name">Peter Wolstenby</h1>
    <p class="contact__title">Au.D. F/NSB</p>
    <p class="contact__address">837 W. Lindell Ave.<br>Brennford, OH 44190</p>
    <ul class="contact__lines">
      <li>
        <svg viewBox="0 0 24 24" aria-hidden="true"><path d="M6.6 10.8a15.1 15.1 0 0 0 6.6 6.6l2.2-2.2c.3-.3.7-.4 1-.2 1.1.4 2.3.6 3.6.6.6 0 1 .4 1 1V20c0 .6-.4 1-1 1A17 17 0 0 1 3 4c0-.6.4-1 1-1h3.5c.6 0 1 .4 1 1 0 1.3.2 2.5.6 3.6.1.3 0 .7-.2 1z"/></svg>
        (440) 683-5127
      </li>
      <li>
        <svg viewBox="0 0 24 24" aria-hidden="true"><path d="M2 6h20v13H2z"/><path d="M2 6l10 7 10-7" fill="none" stroke="#f2f2f2" stroke-width="2"/></svg>
        tolverahearing@postvane.com
      </li>
    </ul>
  </div>

  <svg class="footer-band" viewBox="0 0 600 40" aria-hidden="true">
    <path d="M0 18 H334 C322 25 318 32 302 32 H0 Z" fill="#000000"/>
    <path d="M0 35 H320 C337 35 336 5 353 5 H600 V40 H0 Z" fill="var(--green)"/>
  </svg>
  <span class="footer-band__url">www.tolverahearing.com</span>
</section>

<section class="card card--back" aria-label="Business card back">
  <div class="brand">
    <span class="brand__dot"></span>
    <span class="brand__name">Tolvera Hearing Center</span>
  </div>
</section>

</body>
</html>
```